2-Page Flyer for the Information Session about the Quiet Pathfinder Course

This is a flyer to announce/advertise an evening Information Session about the Quiet Pathfinder Course. This Program aims at mindfully rethinking and redesigning work (and life) for people who feel stuck or not entirely satisfied with their work and/or life (please see draft flyer attached for more details). This Program is property of Bright Meadow, a company that uses a combination of Mindfulness, Design, and Entrepreneurship to help people achieve greater happiness (in their work and lives).

Target Market(s)

People who feel stuck or not entirely satisfied with their work and/or life (please see draft flyer attached for more details)

Font styles to use
Serif
Sans Serif

Colors
ffffff
f37122
33a6d7
acd037

Requirements
Must have
• All of what I will say below is suggestive (I’m not a design expert), and I’m open to divert from it, if it makes sense and feels more interesting.
• I thought initially of a 2-page flyer (please see draft flyer attached). The first page could help people grasp the essence of the event quickly (in 1 or 2 minutes), and then, if they are interested/motivated, they would continue reading through page 2, which has more info about the Program in itself.
• Potential Structure
• Page 1
• . About the Information Session on the Quiet Pathfinder Course
• . Visible Date & Time, Contacts, Venue (and other relevant info)
• . About me (the facilitator)
• Page 2
• . About the Quiet Pathfinder Course
• I include a Powerpoint draft of the flyer with the content. The design is rudimentary and precarious from an aesthetics/organization point of view, and this is mainly where I need help (and maybe in other aspects too!).
• On the flyer, I would like to include:
• . A photo of myself (I attach 1 picture).
• . 1 or 2 beautiful-nature photos (cropped or full). One may have to do with looking at the sky, dreaming, and imagining a new work and life (2 photos with sky and clouds attached). The other has to do with walking the transformation journey (the photo with the person walking through the forest path).
• . bright meadow logo or logos (there are two slightly different ones, that can be used for different purposes). For the first page, I would like the bright meadow logo that has "bright meadow" written on the bottom, with the saying "Stillness, Craft and Venture for Bright Meadow" beneath. This is the main logo. For the 2nd page, you can choose the logo that adapts better.
• - Where it says the "the way out is in" it would be great to have a similar font to the one I attach (see file "Font_the_way_out_is_in.png" and Ankecallig-fg.ttf
Nice to have
• In terms of colours, I would not divert much from the logo colours (and of course white and black). I would like the flyer to be quite white. Almost like fairy-tale white: the white horse, the white snow, the white of the stars, the white heaven. White could be the base colour. White means peace, tranquillity, calm contentment, a smile.
• And then use the other colours. The green of the mindfulness. The blue of the sky, the dreams. And the orange of the sun, the energy, the fire, the action. And maybe the black for text.
• Where it says the "the way out is in" it would be great to have a similar font to the one I attach (see file "Font_the_way_out_is_in".
• I would like this flyer to be a piece of art, in every possible way. Simple, beautiful, ease, light, peaceful, calm happy. Just like the Quiet Pathfinder Course and bright meadow Company that I am creating intends to be. The mission of this Program and Company is to be a designer, a painter (a Picasso) of happier and more fulfilling human lives.
• I am very much looking forward to seeing your proposal(s).

```html
<!DOCTYPE html>
<html lang="en">
<head>
<meta charset="utf-8">
<title>Quiet Pathfinder Course – Information Session Flyer</title>
<link rel="stylesheet" href="https://fonts.googleapis.com/css2?family=Oswald:wght@500;600;700&family=Montserrat:wght@500;600;700&family=Source+Sans+3:ital,wght@0,400;0,600;0,700;1,400;1,600&display=swap">
<style>
:root{
  --white:#ffffff;
  --orange:#f37122;
  --blue:#33a6d7;
  --blue-deep:#2a97d6;
  --green:#acd037;
  --grey:#b5b8bb;
  --ink:#2b2b2b;
  --mist:#e9eef2;
  --paper:#eeeeee;
  --backdrop:#dfe3e6;
}
*{margin:0;padding:0;box-sizing:border-box}
html,body{width:1200px;height:878px;overflow:hidden;background:var(--backdrop)}
body{position:relative;font-family:"Source Sans 3",Arial,sans-serif;color:var(--ink)}
.page{position:absolute;top:36px;width:570px;height:806px;background:var(--white);overflow:hidden;box-shadow:0 2px 10px rgba(0,0,0,.18)}
.page--front{left:18px}
.page--back{left:612px}
.abs{position:absolute}

/* brand */
.brand{display:flex;align-items:center;gap:8px}
.brand__dot{width:34px;height:34px;border-radius:50%;background:var(--blue)}
.brand__name{font-family:"Montserrat",sans-serif;font-weight:500;font-size:25px;color:var(--blue);letter-spacing:-.3px}
.brand__tagline{font-size:7.6px;font-weight:700;font-style:italic;color:var(--ink);text-align:center}

/* front */
.title-band{left:0;top:118px;width:360px;height:174px;background:var(--blue)}
.hero-art{left:210px;top:0;width:360px;height:400px}
.title{left:20px;top:122px;font-family:"Oswald",sans-serif;color:var(--white);font-weight:600;line-height:1}
.title__big{font-size:60px;letter-spacing:1px;display:block}
.title__mid{font-size:36px;letter-spacing:.6px;display:block;margin:3px 0 4px}
.session{left:22px;top:304px;width:530px}
.session__head{font-family:"Oswald",sans-serif;font-weight:500;font-size:22px;color:var(--orange);letter-spacing:.2px}
.facts{list-style:none;margin-top:5px}
.facts li{display:flex;align-items:center;gap:7px;font-size:13.6px;font-weight:700;line-height:18px}
.facts .label{color:var(--orange);font-weight:600}
.facts svg{width:13px;height:13px;flex:none}
.body-copy{font-size:10.3px;line-height:12.6px;color:#3a3a3a}
.section-head{font-family:"Montserrat",sans-serif;font-weight:600;font-size:17px;color:var(--orange)}
.paper{left:0;top:500px;width:570px;height:253px}
.portrait{left:23px;top:550px;width:166px;height:166px}
.facilitator{left:201px;top:534px;width:350px}
.facilitator__role{font-family:"Montserrat",sans-serif;font-size:13px;font-weight:500}
.facilitator__name{font-family:"Montserrat",sans-serif;font-weight:700;font-size:23px;color:var(--orange);line-height:1.1;margin-top:2px}
.facilitator__post{font-size:11px;font-style:italic;font-weight:600;margin-bottom:8px}
.facilitator__bio{font-size:8.8px;line-height:11.4px;text-align:justify;color:#333}
.facilitator__more{font-size:12px;margin-top:9px}
.facilitator__more a{color:var(--blue);font-weight:700;text-decoration:none}

/* footer */
.footer{left:0;top:753px;width:570px;height:53px}
.footer__bg{position:absolute;left:0;top:0;width:570px;height:40px}
.footer__strip{position:absolute;left:0;top:40px;width:570px;height:13px;background:#111;color:#fff;font-family:"Montserrat",sans-serif;font-size:5.6px;letter-spacing:4.2px;padding:3px 0 0 14px}
.phone-badge{position:absolute;left:12px;top:7px;width:26px;height:26px;border-radius:50%;background:#111;display:flex;align-items:center;justify-content:center}
.phone-badge svg{width:14px;height:14px}
.footer__booking{position:absolute;left:50px;top:5px;color:#fff;font-family:"Montserrat",sans-serif}
.footer__booking small{display:block;font-size:7px;font-weight:600;letter-spacing:.2px}
.footer__booking strong{font-size:17px;font-weight:700;line-height:1.1}
.footer__links{position:absolute;top:12px;display:flex;gap:11px;font-family:"Montserrat",sans-serif;font-size:12px;font-weight:600;color:#111}
.footer__links span{display:flex;align-items:center;gap:5px}
.footer__links svg{width:12px;height:12px}

/* back */
.forest{left:0;top:0;width:570px;height:147px;background:linear-gradient(90deg,#2e2a1d 0%,#4a4a2f 30%,#6e7450 50%,#3f3d27 70%,#241f15 100%)}
.quote-credit{left:318px;top:131px;font-size:7.6px;color:var(--orange)}
.back-brand{left:468px;top:111px}
.back-brand .brand__dot{width:18px;height:18px}
.back-brand .brand__name{font-size:12px;line-height:1}
.intro{left:0;top:147px;width:570px;height:147px}
.intro__head{left:0;top:164px;width:570px;text-align:center;font-family:"Montserrat",sans-serif;font-weight:700;font-size:26.5px;color:#fff;letter-spacing:-.2px}
.intro__text{left:26px;top:212px;width:527px;font-size:10.7px;line-height:13.4px;font-style:italic;color:#fff;text-align:justify}
.program{left:0;top:276px;width:570px;height:250px;background:var(--mist)}
.program__head{left:24px;top:315px;font-family:"Montserrat",sans-serif;font-weight:600;font-size:17px;color:var(--blue-deep)}
.program__text{left:24px;top:350px;width:220px;font-size:10.1px;line-height:12.5px;text-align:justify;color:#333}
.program__text p+p{margin-top:10px}
.cycle{left:262px;top:278px;width:308px;height:245px}
.tear{left:0;top:512px;width:570px;height:22px}
.why{left:24px;top:543px;width:245px}
.how{left:291px;top:543px;width:258px}
.col-head{font-family:"Montserrat",sans-serif;font-weight:600;font-size:17px;color:var(--orange);margin-bottom:3px}
.steps{list-style:none;margin-top:12px}
.steps li{position:relative;padding-left:18px;font-size:10.2px;line-height:12.5px;color:#333}
.steps li::before{content:counter(item);counter-increment:item;position:absolute;left:0;top:2px;width:10px;height:10px;border-radius:50%;font-size:7px;line-height:10px;text-align:center;color:#fff;font-weight:700}
.steps{counter-reset:item}
.steps--orange li::before{background:var(--orange)}
.steps--green li::before{background:var(--green)}
.how .closing{margin-top:8px}
</style>
</head>
<body>

<!-- FRONT PAGE -->
<section class="page page--front">
  <svg class="abs hero-art" viewBox="0 0 360 400" role="img" aria-label="Painted circle of nature photos: blue sky with clouds, orange sunset sky and green hills">
    <defs>
      <linearGradient id="heroGrad" x1="0" y1="0" x2="1" y2="1">
        <stop offset="0" stop-color="#5fb6e6"/>
        <stop offset=".42" stop-color="#bfe0f2"/>
        <stop offset=".55" stop-color="#f29a52"/>
        <stop offset=".7" stop-color="#e9813a"/>
        <stop offset=".78" stop-color="#7fa63a"/>
        <stop offset="1" stop-color="#3f7d22"/>
      </linearGradient>
    </defs>
    <circle cx="198" cy="194" r="178" fill="url(#heroGrad)"/>
  </svg>
  <div class="abs title-band"></div>

  <div class="abs" style="left:0;top:38px;width:290px">
    <div class="brand" style="justify-content:center">
      <span class="brand__dot"></span>
      <span class="brand__name">bright meadow</span>
    </div>
    <p class="brand__tagline" style="margin-top:8px">Stillness, Craft and Venture for Bright Meadow</p>
  </div>

  <h1 class="abs title">
    <span class="title__big">QUIET</span>
    <span class="title__mid">PATHFINDER</span>
    <span class="title__big">COURSE</span>
  </h1>

  <div class="abs session">
    <h2 class="session__head">FREE INFORMATION SESSION</h2>
    <ul class="facts">
      <li><svg viewBox="0 0 14 14"><rect x="1" y="2.5" width="12" height="10.5" rx="1" fill="none" stroke="#33a6d7" stroke-width="1.5"/><line x1="1" y1="5.5" x2="13" y2="5.5" stroke="#33a6d7" stroke-width="1.5"/><line x1="4" y1="1" x2="4" y2="4" stroke="#33a6d7" stroke-width="1.5"/><line x1="10" y1="1" x2="10" y2="4" stroke="#33a6d7" stroke-width="1.5"/></svg><span><span class="label">Date:</span> Thursday 5th September 2019,</span></li>
      <li><svg viewBox="0 0 14 14"><circle cx="7" cy="7" r="5.8" fill="none" stroke="#33a6d7" stroke-width="1.5"/><path d="M7 3.8V7l2.4 1.5" fill="none" stroke="#33a6d7" stroke-width="1.5"/></svg><span><span class="label">Time:</span> 19:30 to 21:00</span></li>
      <li><svg viewBox="0 0 14 14"><path d="M7 13S2.5 8 2.5 5.2a4.5 4.5 0 0 1 9 0C11.5 8 7 13 7 13z" fill="#33a6d7"/><circle cx="7" cy="5.2" r="1.6" fill="#fff"/></svg><span><span class="label">Venue:</span> Tidewell Coworking, C/ Almendro 14, Barcelona</span></li>
    </ul>
    <p class="body-copy" style="margin-top:9px">The purpose of this free Information Session is to give you a real insight into the Quiet Pathfinder Course and how it can help you make the most of your professional and personal life.</p>
    <h3 class="section-head" style="margin-top:14px">Who can come</h3>
    <p class="body-copy" style="margin-top:5px">Whether you come on your own, or with friends or family, you'll be warmly welcomed. The session will take place on Thursday the 5th September 2019, from 19:30 to 21:00, at Tidewell Coworking. Please see information below to get in contact or to book a seat.</p>
  </div>

  <svg class="abs paper" viewBox="0 0 570 253" preserveAspectRatio="none" aria-hidden="true">
    <path d="M0 12 L40 8 L90 13 L140 7 L200 12 L260 6 L320 12 L380 8 L440 13 L500 7 L570 11 V253 H0Z" fill="#ececec"/>
  </svg>

  <svg class="abs portrait" viewBox="0 0 166 166" role="img" aria-label="Portrait photo of the facilitator">
    <defs>
      <radialGradient id="portraitGrad" cx=".5" cy=".45" r=".6">
        <stop offset="0" stop-color="#d8d4d0"/>
        <stop offset="1" stop-color="#8a96a3"/>
      </radialGradient>
    </defs>
    <circle cx="83" cy="83" r="80" fill="url(#portraitGrad)" stroke="#fff" stroke-width="3"/>
  </svg>

  <div class="abs facilitator">
    <p class="facilitator__role">Facilitator</p>
    <p class="facilitator__name">DR MATEO RIVAS</p>
    <p class="facilitator__post">Visiting Research Fellow, Harlow Coast University</p>
    <p class="facilitator__bio">Mateo joined Harlow Coast University's School of Management as a Lecturer in Entrepreneurship in 2015. He completed his PhD in Entrepreneurship at Kelburn Business School in 2014, receiving the prestigious Fenwick Doctoral Dissertation Award. He began his business career as a Production Engineer for Norvane Industries, and later as a Sales Engineer. After his MBA, he served as a Strategy Consultant for Ribeira School of Management. Originally from Portugal, Mateo enjoys designing and launching new ideas, international communities, mindfulness retreats, and musical improvisation. He nurtures a close connection to Willow Hill Mindfulness Centre, where he has practiced and volunteered over 9 months. He has a broad experience of sharing the benefits of mindfulness with others.</p>
    <p class="facilitator__more">More about the facilitator: <a>www.profilehub.net/in/mateorivas</a></p>
  </div>

  <div class="abs footer">
    <svg class="footer__bg" viewBox="0 0 570 40" preserveAspectRatio="none" aria-hidden="true">
      <rect width="570" height="40" fill="#a5cd39"/>
      <polygon points="0,0 218,0 200,40 0,40" fill="#2f9fdc"/>
    </svg>
    <span class="phone-badge"><svg viewBox="0 0 16 16"><path d="M4 1.5l2.3 3-1.4 1.6c.7 1.8 2.2 3.3 4 4l1.6-1.4 3 2.3-1.3 2.4C7.2 13.1 2.9 8.8 1.6 3z" fill="#fff"/></svg></span>
    <div class="footer__booking"><small>INFORMATION &amp; BOOKING:</small><strong>+34 600 412 375</strong></div>
    <div class="footer__links" style="left:225px">
      <span><svg viewBox="0 0 12 12"><circle cx="6" cy="6" r="5.5" fill="#111"/><path d="M1 6h10M6 .8c-2 2.8-2 7.6 0 10.4M6 .8c2 2.8 2 7.6 0 10.4" stroke="#a5cd39" stroke-width=".8" fill="none"/></svg>www.brightmeadow.io</span>
      <span><svg viewBox="0 0 12 12"><circle cx="6" cy="6" r="5.5" fill="#111"/><rect x="3" y="4" width="6" height="4.2" fill="none" stroke="#fff" stroke-width=".8"/><path d="M3 4l3 2.3L9 4" fill="none" stroke="#fff" stroke-width=".8"/></svg>info@brightmeadow.io</span>
    </div>
    <div class="footer__strip">VIDEO CALL AND MESSAGING</div>
  </div>
</section>

<!-- BACK PAGE -->
<section class="page page--back">
  <div class="abs forest" role="img" aria-label="Photo of a person walking down a long forest path, with the hand-lettered words 'the way out is in'"></div>
  <p class="abs quote-credit">Zen Master Tuan An Lo</p>
  <div class="abs brand back-brand">
    <span class="brand__dot"></span>
    <span class="brand__name">bright<br>meadow</span>
  </div>

  <svg class="abs intro" viewBox="0 0 570 147" preserveAspectRatio="none" aria-hidden="true">
    <polygon points="0,0 570,0 570,129 298,129 282,147 266,129 0,129" fill="#2f9fdc"/>
  </svg>
  <div class="abs program"></div>
  <svg class="abs" style="left:0;top:276px" width="570" height="18" viewBox="0 0 570 18" aria-hidden="true">
    <polygon points="0,0 570,0 570,0 298,0 282,18 266,0" fill="#2f9fdc"/>
  </svg>
  <h2 class="abs intro__head">What is Mindful Entrepreneurship</h2>
  <p class="abs intro__text">Being mindful means being aware and awake. Entrepreneurship is the creation of a new form of organising. The Quiet Pathfinder Course is then the process of creating or redesigning your work and life with awareness, in a way that is reflective of you, of your passions and values, thus conducing to a greater sense of fulfilment and happiness.</p>

  <h3 class="abs program__head">The Program</h3>
  <div class="abs program__text">
    <p><strong>The Quiet Pathfinder Course</strong> is a <strong>4-month long transformative journey</strong> designed for people who feel stuck or not entirely satisfied with their professional and/or personal life. It will be of benefit for everyone, at any stage.</p>
    <p>The Program entails a five-hour workshop each month, complemented by two-hour weekly peer support meetings. It combines mindfulness techniques, design thinking methodology, and entrepreneurship frameworks.</p>
  </div>

  <svg class="abs cycle" viewBox="0 0 308 245" aria-label="Program cycle: Insight, Design, Execute, Present workshops linked by weekly peer support meetings">
    <defs>
      <marker id="arrowHead" viewBox="0 0 6 6" refX="3" refY="3" markerWidth="4" markerHeight="4" orient="auto"><path d="M0 0L6 3L0 6z" fill="context-stroke"/></marker>
    </defs>
    <g font-family="Source Sans 3, Arial, sans-serif" text-anchor="middle">
      <circle cx="142" cy="57" r="43" fill="#acd037" stroke="#fff" stroke-width="3"/>
      <text x="142" y="50" font-size="8" fill="#fff" font-weight="600">Workshop 1</text>
      <text x="142" y="65" font-family="Oswald, sans-serif" font-size="14" font-weight="600" fill="#fff">INSIGHT</text>
      <text x="142" y="77" font-size="8" font-style="italic" fill="#fff">(5 hours)</text>

      <circle cx="218" cy="126" r="43" fill="#2f9fdc" stroke="#fff" stroke-width="3"/>
      <text x="218" y="119" font-size="8" fill="#fff" font-weight="600">Workshop 2</text>
      <text x="218" y="134" font-family="Oswald, sans-serif" font-size="14" font-weight="600" fill="#fff">DESIGN</text>
      <text x="218" y="146" font-size="8" font-style="italic" fill="#fff">(5 hours)</text>

      <circle cx="138" cy="185" r="43" fill="#f37122" stroke="#fff" stroke-width="3"/>
      <text x="138" y="178" font-size="8" fill="#fff" font-weight="600">Workshop 3</text>
      <text x="138" y="193" font-family="Oswald, sans-serif" font-size="14" font-weight="600" fill="#fff">EXECUTE</text>
      <text x="138" y="205" font-size="8" font-style="italic" fill="#fff">(5 hours)</text>

      <circle cx="69" cy="126" r="43" fill="#b5b8bb" stroke="#fff" stroke-width="3"/>
      <text x="69" y="119" font-size="8" fill="#fff" font-weight="600">Workshop 4</text>
      <text x="69" y="134" font-family="Oswald, sans-serif" font-size="14" font-weight="600" fill="#fff">PRESENT</text>
      <text x="69" y="146" font-size="8" font-style="italic" fill="#fff">(5 hours)</text>

      <path d="M184 58 q10 2 12 14" fill="none" stroke="#acd037" stroke-width="2.5" marker-end="url(#arrowHead)"/>
      <path d="M218 172 q-2 12 -14 14" fill="none" stroke="#2f9fdc" stroke-width="2.5" marker-end="url(#arrowHead)"/>
      <path d="M94 185 q-10 -2 -12 -13" fill="none" stroke="#f37122" stroke-width="2.5" marker-end="url(#arrowHead)"/>
      <path d="M84 80 q2 -12 12 -14" fill="none" stroke="#9a9da0" stroke-width="2.5" marker-end="url(#arrowHead)"/>

      <g font-size="7.8" font-weight="700" font-style="italic" fill="#222">
        <text x="46" y="53">WPS meetings</text>
        <text x="40" y="193">WPS meetings</text>
        <text x="272" y="193">WPS meetings</text>
        <text x="266" y="44" font-style="normal">Weekly Peer Support</text>
        <text x="266" y="54" font-weight="600">(WPS) meetings</text>
        <text x="266" y="64" font-weight="600">(2 hours)</text>
      </g>
    </g>
  </svg>

  <svg class="abs tear" viewBox="0 0 570 22" preserveAspectRatio="none" aria-hidden="true">
    <path d="M0 12 L45 8 L95 13 L150 7 L210 12 L270 6 L330 12 L390 8 L450 13 L510 7 L570 11 V22 H0Z" fill="#fff"/>
  </svg>

  <div class="abs why">
    <h3 class="col-head">Why</h3>
    <p class="body-copy" style="font-size:10.2px;text-align:justify">Many people are not satisfied with their work, but they don't know what to do about it. This Program offers you a safe place to conduct your inner journey with collective support, helping you reflect, design, and (very likely) do something about it. It aims at:</p>
    <ol class="steps steps--orange">
      <li>Increasing awareness, clarity and confidence</li>
      <li>Having a deeper <strong><em>insight</em></strong> on what makes you happier and what you want</li>
      <li>Developing a clear <strong><em>design</em></strong> integrating your intended work and life</li>
      <li>Start <strong><em>executing</em></strong> this design</li>
    </ol>
  </div>

  <div class="abs how">
    <h3 class="col-head">How</h3>
    <p class="body-copy" style="font-size:10.2px">This Program differs from existing entrepreneurial programs in many ways:</p>
    <ol class="steps steps--green">
      <li>Uses mindfulness and self analysis to look deeply into yourself</li>
      <li>Design and execution decisions are based on happiness rather than (only) financials</li>
      <li>Holistic and inclusive design process, integrating work and life, and building synergies between your different parts</li>
    </ol>
    <p class="body-copy closing" style="font-size:10.2px">The Program's format includes lectures, individual work, group sharing, guided activities, experiential exercises, video, audio, handouts and other resources.</p>
  </div>

  <div class="abs footer">
    <svg class="footer__bg" viewBox="0 0 570 40" preserveAspectRatio="none" aria-hidden="true">
      <rect width="570" height="40" fill="#a5cd39"/>
      <polygon points="0,0 218,0 200,40 0,40" fill="#2f9fdc"/>
    </svg>
    <span class="phone-badge"><svg viewBox="0 0 16 16"><path d="M4 1.5l2.3 3-1.4 1.6c.7 1.8 2.2 3.3 4 4l1.6-1.4 3 2.3-1.3 2.4C7.2 13.1 2.9 8.8 1.6 3z" fill="#fff"/></svg></span>
    <div class="footer__booking" style="top:9px"><strong>+34 600 412 375</strong></div>
    <div class="footer__links" style="left:226px">
      <span><svg viewBox="0 0 12 12"><circle cx="6" cy="6" r="5.5" fill="#111"/><path d="M1 6h10M6 .8c-2 2.8-2 7.6 0 10.4M6 .8c2 2.8 2 7.6 0 10.4" stroke="#a5cd39" stroke-width=".8" fill="none"/></svg>www.brightmeadow.io</span>
      <span><svg viewBox="0 0 12 12"><circle cx="6" cy="6" r="5.5" fill="#111"/><rect x="3" y="4" width="6" height="4.2" fill="none" stroke="#fff" stroke-width=".8"/><path d="M3 4l3 2.3L9 4" fill="none" stroke="#fff" stroke-width=".8"/></svg>info@brightmeadow.io</span>
    </div>
    <div class="footer__strip">VIDEO CALL AND MESSAGING</div>
  </div>
</section>

</body>
</html>
```